wardrobe/costume stylist needs good business card for own business

Hi:)

I'm wanting a business card for my company. I am a freelance stylist.

I do wardrobe/costume stylist to TV commercials; Films; Fashion and Lifestyle shoots.

I'd like a design based around my name Rosalind Parfrey written nicely, maybe a colour? Up to you?!

I've attached a couple of images of business cards I like
.... be creative and have fun!

Thank you :)

Reason: I was trying to get my new business card ready for before I headed overseas Friday morning but I don't think that was realistic so I'd like to extend the deadline to give time to the project. Thank you

Hi designers:) Thank you for all your designs, I've extended the deadline until Sunday, so there's a bit more time. I've attached 3 pictures of business cards which I quite like, please take a look to see if it can be of help in your process. I like the pale plain or patterned background with dark font and the dark plain or patterned background with the pale font the motifs the feminine fonts the plain fonts I like the idea of playing with a circle or some shape on one side of the card with my name or initials as in the picture I have on my post could you play around with this idea a bit please? Thank you all for the work you've done :) Rosa

Hi I am working overseas til Saturday night sorry for no feedback until I teturn Thanks :) Rosa

Hi designers, Thank you all so much for submitting your designs, I really appreciate your input into my project :) I'm sorry I didn't get to respond to some comments, and give feedback. I didn't back from being away until later than I expected, and the deadline had passed then, so apologies. Thanks to you all again for all your really good designs :) Rosa

Target Market(s)

I am a freelance stylist my target audience is producers, production companies, photographers, directors...

Industry/Entity Type

Business

Requirements
Must have
• Rosalind Parfrey
Stylist or Wardrobe Stylist

email rosaparfrey@mailbox-example.co.nz
Mobile 0218467193

(Don't have to use the words 'email' and 'mobile')
Nice to have
• Would like it to be double sided
Like B & W
Like pale colour background with dark font or white font
Like dark colour background with pale font
Should not have
• I would prefer it not to incorporate pictures

```html
<!DOCTYPE html>
<html lang="en">
<head>
<meta charset="utf-8">
<title>Rosalind Parfrey – Stylist business card</title>
<link rel="stylesheet" href="https://fonts.googleapis.com/css2?family=Pinyon+Script&family=Open+Sans:wght@300;400&display=swap">
<style>
  :root {
    --backdrop-light: #f4f4f4;
    --backdrop-dark: #c9c9c9;
    --card-cream: #e9e1b3;
    --ink-grey: #6e6e6e;
    --ink-white: #ffffff;
    --monogram-tone: #cfc9a6;
  }
  * { margin: 0; padding: 0; box-sizing: border-box; }
  html, body { width: 1200px; height: 1000px; overflow: hidden; }
  body {
    position: relative;
    background: radial-gradient(ellipse at 50% 45%, var(--backdrop-light) 0%, #e6e6e6 55%, var(--backdrop-dark) 100%);
    font-family: "Open Sans", sans-serif;
  }
  .card {
    position: absolute;
    background: var(--card-cream);
    box-shadow: 0 6px 14px rgba(0,0,0,0.12);
  }
  .card--back {
    left: 470px; top: 190px;
    width: 420px; height: 233px;
  }
  .card--front {
    left: 270px; top: 470px;
    width: 540px; height: 300px;
  }
  .monogram {
    position: absolute;
    right: 18px; top: 22px;
    width: 70px; height: 190px;
  }
  .card__name {
    position: absolute;
    left: 44px; top: 62px;
    font-family: "Pinyon Script", cursive;
    font-size: 50px;
    font-weight: 400;
    color: var(--ink-white);
    white-space: nowrap;
  }
  .card__role {
    position: absolute;
    left: 50px; top: 186px;
    font-size: 27px;
    font-weight: 300;
    color: var(--ink-grey);
  }
  .card__contact {
    position: absolute;
    right: 40px; top: 150px;
    text-align: right;
    font-size: 14px;
    font-weight: 300;
    line-height: 1.55;
    color: var(--ink-grey);
  }
</style>
</head>
<body>
  <section class="card card--back" aria-label="Card back">
    <svg class="monogram" viewBox="0 0 70 190" role="img" aria-label="Script monogram of the initials R and P">
      <rect x="0" y="0" width="70" height="190" rx="35" fill="var(--monogram-tone)"/>
    </svg>
  </section>

  <section class="card card--front" aria-label="Card front">
    <h1 class="card__name">Rosalind Parfrey</h1>
    <p class="card__role">Stylist</p>
    <p class="card__contact">
      rosaparfrey@mailbox-example.co.nz<br>
      0218467193
    </p>
  </section>
</body>
</html>
```